Property Finance Company - Orbin Funding Limited

Background: Orbin Funding Group Limited is a private property finance company. Orbin Funding Group has capital to directly fund first mortgage, mezzanine and preferred equity financing. We also acquire performing, sub-performing and distressed debt.

Orbin Fundings management philosophy emphasises expertise, innovation, wisdom, honesty and competitiveness. Orbin Funding are not finance brokers - we provide debt funding to the commercial property and residential development sectors. Our process is built from experience and cumutavely Orbin Fundings Directors have in excess of 60 years wisdom.

The aim of the website will be to increase brand awareness, provide clients with comfort around our level of skill and background on who we are, generate more sales, and provide examples of projects that we have funded.

The website is a new product launch, and we need to use our Orbin Funding logo that has just been designed. We like a dark background, and either black/silver/grey/ jade green, or black/gold/jade green colours.

Our unique advantages are that we have fast turnaround times, we can solve clients funding problems and we know what we are doing. Our target audience will be viewing the website on both desktop and mobile devices.

We would like to have the following pages:

Home
About
Team
Services
Project Experience
Contact

Competitors Website: http://www.tarvolo.example/

We would also like to have the option of video footage in our website, as you can see in our competitors website.

Overall we want a really slick, elegant but modern website that is better than www.tarvolo.example

Target Market(s)

Finance borrowers, property developers, accountants, lawyers, businesspeople, high net worth people

Industry/Entity Type

Finance

Requirements
Must have
• Please see project description
Nice to have
Should not have

```html
<!DOCTYPE html>
<html lang="en">
<head>
<meta charset="utf-8">
<title>Orbin Funding Group – Private Property Finance</title>
<link href="https://fonts.googleapis.com/css2?family=Lato:wght@400;700;900&display=swap" rel="stylesheet">
<style>
:root{
  --jade:#1f9a57;
  --jade-text:#1d9152;
  --ink:#222222;
  --footer:#242424;
  --white:#ffffff;
  --muted:#9a9a9a;
  --body-text:#3a3a3a;
  --panel:rgba(240,240,240,.78);
  --panel-line:#d6d6d6;
  --silver-a:#d8d8d8;
  --silver-b:#bfbfbf;
}
*{box-sizing:border-box;margin:0;padding:0}
html,body{width:1200px;height:2195px;overflow:hidden}
body{font-family:"Lato",sans-serif;color:var(--body-text);background:var(--silver-a);position:relative}
a{color:inherit;text-decoration:none}

/* hero */
.hero{position:absolute;left:0;top:0;width:1200px;height:662px;
  background:linear-gradient(120deg,#5c5a57 0%,#8a8580 35%,#6e6a66 60%,#4a4744 100%)}
.hero-shade{position:absolute;inset:0;background:rgba(20,20,20,.28)}
.brand{position:absolute;left:76px;top:52px;width:152px;text-align:center;color:var(--white)}
.brand-mark{width:34px;height:34px;border-radius:50%;background:var(--white);margin:0 auto 12px}
.brand-name{font-size:21px;font-weight:700;letter-spacing:.5px;line-height:1.1}
.nav{position:absolute;top:64px;right:40px;display:flex;align-items:center;gap:0}
.nav a{display:block;height:49px;line-height:49px;padding:0 25px;font-size:13px;color:var(--white);text-transform:uppercase;letter-spacing:.3px}
.nav a.is-active{background:var(--jade);font-weight:900}
.hero-title{position:absolute;left:0;right:0;top:282px;text-align:center;color:var(--white);font-size:42px;font-weight:900;line-height:1;text-shadow:0 2px 6px rgba(0,0,0,.3)}
.story{position:absolute;left:76px;top:532px;display:flex;align-items:center;gap:12px;color:var(--white);font-size:41px;font-weight:400;letter-spacing:.5px}
.story svg{width:46px;height:46px}
.scroll-down{position:absolute;left:588px;top:592px;width:24px;height:24px}

/* main */
.main{position:absolute;left:0;top:662px;width:1200px;height:1262px;
  background:repeating-linear-gradient(0deg,rgba(255,255,255,.12) 0 1px,rgba(0,0,0,.03) 1px 3px),linear-gradient(180deg,var(--silver-a),#cfcfcf 50%,var(--silver-b))}
.tag{position:absolute;left:75px;height:51px;line-height:51px;padding-left:20px;color:var(--white);background:var(--jade);font-size:26px;font-weight:700;text-transform:uppercase;clip-path:polygon(0 0,100% 0,calc(100% - 25px) 100%,0 100%)}
.tag-welcome{top:55px;width:423px}
.tag-services{top:408px;width:256px}
.welcome{position:absolute;left:75px;top:121px;width:1050px;height:247px;background:var(--panel);border:1px solid var(--panel-line)}
.welcome-copy{position:absolute;left:20px;top:18px;width:700px;font-size:13.5px;line-height:23px;color:var(--body-text)}
.welcome-copy p+p{margin-top:5px}
.btn-dark{position:absolute;left:20px;top:178px;width:157px;height:46px;line-height:46px;text-align:center;background:var(--ink);color:var(--white);font-size:14px;font-weight:700;text-transform:uppercase}
.welcome-brand{position:absolute;right:30px;top:70px;width:290px;text-align:center;color:#5a5a5a}
.welcome-brand .name{font-size:38px;font-weight:400;letter-spacing:1px;line-height:1.1}

.cards{position:absolute;left:75px;top:482px;display:flex;gap:32px}
.card{width:329px;height:273px;background:var(--panel);border:1px solid var(--panel-line);padding:22px 20px 0 20px;position:relative}
.card-head{display:flex;gap:14px;align-items:flex-start;height:52px}
.card-head svg{width:34px;height:34px;flex:none;fill:#2b2b2b}
.card-title{font-size:16px;font-weight:900;color:var(--jade-text);text-transform:uppercase;line-height:21px}
.card p{margin-top:14px;font-size:13.5px;line-height:24px;color:var(--body-text)}
.card-link{position:absolute;left:20px;bottom:30px;font-size:13px;font-weight:900;text-transform:uppercase;text-decoration:underline;color:var(--ink)}

.tile{position:absolute;color:var(--white);font-size:20px;font-weight:700;text-transform:uppercase;padding:26px 0 0 28px;border:1px solid #b5b5b5}
.tile-projects{left:75px;top:784px;width:690px;height:445px;background:linear-gradient(180deg,#4f6b84 0%,#7f8c96 45%,#3c3f44 100%)}
.tile-team{left:793px;top:784px;width:332px;height:209px;background:linear-gradient(180deg,#9aa6b2 0%,#8b8580 60%,#6d7480 100%);padding-left:26px}
.tile-contact{left:793px;top:1019px;width:332px;height:210px;background:linear-gradient(135deg,#6f7f84 0%,#a3abad 55%,#7a8385 100%);padding-left:26px}

/* footer */
.footer{position:absolute;left:0;top:1924px;width:1200px;height:271px;background:var(--footer);color:#d8d8d8}
.footer-brand{position:absolute;left:76px;top:48px;width:132px;text-align:center;color:var(--white)}
.footer-brand .brand-mark{width:28px;height:28px;margin-bottom:10px}
.footer-brand .brand-name{font-size:18px}
.copyright{position:absolute;left:76px;top:170px;font-size:13px;line-height:21px;color:var(--muted)}
.col{position:absolute;top:42px}
.col h3{font-size:15px;font-weight:700;color:var(--white);text-transform:uppercase;margin-bottom:12px;letter-spacing:.2px}
.col-sitemap{left:363px}
.col-sitemap li{list-style:none;font-size:14px;line-height:26.6px}
.col-contact{left:600px;width:230px}
.col-contact .addr{font-size:13.5px;line-height:20px;margin-bottom:6px}
.contact-row{display:flex;align-items:center;gap:14px;font-size:14px;line-height:26.6px}
.contact-row svg{width:14px;height:14px;fill:#e0e0e0;flex:none}
.col-email{left:899px;width:227px}
.signup{display:flex;height:40px}
.signup input{width:188px;height:40px;border:0;padding:0 14px;font:12px "Lato",sans-serif;color:#333;background:var(--white)}
.signup button{width:38px;height:40px;border:0;background:var(--jade);color:var(--white);font:900 14px "Lato",sans-serif}
.follow{margin-top:20px}
.social{display:flex;gap:14px;margin-top:-2px}
.social span{width:20px;height:20px;border-radius:50%;background:#cfcfcf}
</style>
</head>
<body>

<header class="hero" role="img" aria-label="Photograph of business advisers meeting clients at an office desk with a laptop and coffee cups">
  <div class="hero-shade"></div>
  <div class="brand">
    <div class="brand-mark"></div>
    <div class="brand-name">ORBIN FUNDING GROUP</div>
  </div>
  <nav class="nav">
    <a class="is-active" href="#">Home</a>
    <a href="#">About</a>
    <a href="#">Team</a>
    <a href="#">Services</a>
    <a href="#">Project Experience</a>
    <a href="#">Contact</a>
  </nav>
  <h1 class="hero-title">Orbin Funding Group Limited is a private<br>property finance company.</h1>
  <a class="story" href="#">
    <svg viewBox="0 0 46 46"><circle cx="23" cy="23" r="20" fill="none" stroke="#fff" stroke-width="4"/><path d="M18 13 L33 23 L18 33 Z" fill="#fff"/></svg>
    OUR STORY
  </a>
  <svg class="scroll-down" viewBox="0 0 24 24"><path d="M3 7 L12 16 L21 7" fill="none" stroke="#fff" stroke-width="4"/></svg>
</header>

<main class="main">
  <h2 class="tag tag-welcome">Welcome to Orbin Funding</h2>
  <section class="welcome">
    <div class="welcome-copy">
      <p>Orbin Funding Group Limited is a private property finance company. Orbin Funding Group has capital to directly fund first mortgage, mezzanine and preferred equity financing. We also acquire performing, sub-performing and distressed debt.</p>
      <p>Orbin Fundings management philosophy emphasises expertise, innovation, wisdom, honesty and competitiveness. Orbin Funding are not finance brokers - we provide debt funding to the commercial property and residential development sectors.</p>
    </div>
    <a class="btn-dark" href="#">Read More</a>
    <div class="welcome-brand"><div class="name">ORBIN FUNDING GROUP</div></div>
  </section>

  <h2 class="tag tag-services">Services</h2>
  <div class="cards">
    <article class="card">
      <div class="card-head">
        <svg viewBox="0 0 34 34"><circle cx="17" cy="10" r="8"/><path d="M2 34 C2 22 8 19 17 19 C26 19 32 22 32 34 Z"/></svg>
        <h3 class="card-title">Private Property<br>Finance</h3>
      </div>
      <p>Aliquam molestie, mi et imperdiet euismod, dui purus auctor tellus, et interdum lacus lectus et ante. Sed accumsan sollicitudin sapien, sit amet adipiscing turpis gravida ac porttitor lectus..</p>
      <a class="card-link" href="#">Read More</a>
    </article>
    <article class="card">
      <div class="card-head">
        <svg viewBox="0 0 34 34"><path d="M5 1 H29 V34 H5 Z M9 5 V9 H13 V5 Z M15 5 V9 H19 V5 Z M21 5 V9 H25 V5 Z M9 12 V16 H13 V12 Z M15 12 V16 H19 V12 Z M21 12 V16 H25 V12 Z M9 19 V23 H13 V19 Z M15 19 V23 H19 V19 Z M21 19 V23 H25 V19 Z M9 26 V30 H13 V26 Z M15 26 V34 H19 V26 Z M21 26 V30 H25 V26 Z" fill-rule="evenodd"/></svg>
        <h3 class="card-title">Commercial Property<br>Debt Fund</h3>
      </div>
      <p>Aliquam molestie, mi et imperdiet euismod, dui purus auctor tellus, et interdum lacus lectus et ante. Sed accumsan sollicitudin sapien, sit amet adipiscing turpis gravida ac porttitor lectus..</p>
      <a class="card-link" href="#">Read More</a>
    </article>
    <article class="card">
      <div class="card-head">
        <svg viewBox="0 0 34 34"><path d="M17 2 L34 17 L30 17 L30 32 L21 32 L21 22 L13 22 L13 32 L4 32 L4 17 L0 17 Z"/></svg>
        <h3 class="card-title">Residential Development<br>Sectors.</h3>
      </div>
      <p>Aliquam molestie, mi et imperdiet euismod, dui purus auctor tellus, et interdum lacus lectus et ante. Sed accumsan sollicitudin sapien, sit amet adipiscing turpis gravida ac porttitor lectus..</p>
      <a class="card-link" href="#">Read More</a>
    </article>
  </div>

  <a class="tile tile-projects" href="#" role="img" aria-label="Photograph looking up at glass office towers against a cloudy sky">Project Experience</a>
  <a class="tile tile-team" href="#" role="img" aria-label="Photograph of a smiling team of five colleagues">Team</a>
  <a class="tile tile-contact" href="#" role="img" aria-label="Photograph of a hand holding a glass globe over a laptop keyboard">Contact</a>
</main>

<footer class="footer">
  <div class="footer-brand">
    <div class="brand-mark"></div>
    <div class="brand-name">ORBIN FUNDING GROUP</div>
  </div>
  <p class="copyright">Copyright © 2017. Company Name<br>All Right Reserved</p>

  <div class="col col-sitemap">
    <h3>Site Map</h3>
    <ul>
      <li><a href="#">Home</a></li>
      <li><a href="#">About</a></li>
      <li><a href="#">Team</a></li>
      <li><a href="#">Services</a></li>
      <li><a href="#">Project Experience</a></li>
      <li><a href="#">Contact</a></li>
    </ul>
  </div>

  <div class="col col-contact">
    <h3>Contact Info</h3>
    <p class="addr">412 Kelvane Street<br>Dunmore, DN7 3QX</p>
    <div class="contact-row"><svg viewBox="0 0 14 14"><path d="M3 0 L5.5 3.5 L4 5 C5 7 7 9 9 10 L10.5 8.5 L14 11 L12 14 C6 13 1 8 0 2 Z"/></svg>1-800-555-0148</div>
    <div class="contact-row"><svg viewBox="0 0 14 14"><path d="M0 2 H14 V12 H0 Z M1 3 L7 8 L13 3" fill-rule="evenodd"/></svg>hello@orbinfunding.example</div>
    <div class="contact-row"><svg viewBox="0 0 14 14"><path d="M7 0 C10 0 12 2 12 5 C12 8 7 14 7 14 C7 14 2 8 2 5 C2 2 4 0 7 0 Z M7 3 A2 2 0 1 0 7 7 A2 2 0 1 0 7 3 Z" fill-rule="evenodd"/></svg>Map Location</div>
  </div>

  <div class="col col-email">
    <h3>Email Sign Up</h3>
    <form class="signup"><input type="email" placeholder="Enter Email Address"><button type="button">GO</button></form>
    <h3 class="follow">Follow Us</h3>
    <div class="social"><span></span><span></span><span></span><span></span><span></span></div>
  </div>
</footer>

</body>
</html>
```